Helen's 40th Invitation

I need an invitation designed for a 40th birthday in Singapore. The theme is a "long lunch", set in a colonial garden (black and white house - Singapore style if you want to Google or Bing it).
Look and feel should be simple, elegant, stylish, bold, fresh, minimalist. Nothing fussy, intricate, formal or too colourful. No intials, not wedding-like, minimal colour (no golds).
Setting will be garden setting with champagne, white marquee, white table cloths, long trestle tables, fresh white floowers (lilys or hydrangas).
Format should be PC friendly (jpeg, gif, pdf etc).
Size is flexible to accomodate design - it will be emailed as an attachment.
Details to include:
- Saturday, 27th November, 2010
Time - From 1pm.
Address - 214 Fernbrook Rise, Singapore
Dress: Garden Glam
RSVP - jolwen@quarlixmail.com by 13 November, 2010

```html
<!DOCTYPE html>
<html lang="en">
<head>
<meta charset="utf-8">
<title>Long Lunch – Helen's 40th</title>
<link rel="stylesheet" href="https://fonts.googleapis.com/css2?family=Bodoni+Moda:wght@400&family=Quicksand:wght@500&family=Arimo:wght@400;700&display=swap">
<style>
  :root {
    --page: #ffffff;
    --earth: #3c2415;
    --ink: #ffffff;
    --leaf-deep: #0e7a3e;
    --leaf-soft: #5fa883;
  }
  * { margin: 0; padding: 0; box-sizing: border-box; }
  html, body {
    width: 1200px;
    height: 900px;
    overflow: hidden;
    background: var(--page);
  }
  .invitation {
    position: absolute;
    left: 70px;
    top: 166px;
    width: 1056px;
    height: 534px;
    background: var(--earth);
    color: var(--ink);
    font-family: "Arimo", Arial, sans-serif;
    overflow: hidden;
  }
  .vine-area {
    position: absolute;
    left: 0;
    top: 0;
    width: 1056px;
    height: 400px;
  }
  .title {
    position: absolute;
    left: 0;
    top: 0;
    width: 1056px;
    height: 260px;
  }
  .title text {
    font-family: "Bodoni Moda", "Didot", serif;
    font-size: 232px;
    fill: var(--ink);
  }
  .occasion {
    position: absolute;
    right: 30px;
    top: 178px;
    font-family: "Quicksand", "Century Gothic", sans-serif;
    font-weight: 500;
    font-size: 52px;
    line-height: 1;
  }
  .details {
    position: absolute;
    top: 258px;
    font-size: 24px;
    line-height: 40px;
  }
  .details strong { font-weight: 700; }
  .details--when { left: 24px; }
  .details--venue { left: 386px; }
  .details--dress { left: 806px; }
  .rsvp {
    position: absolute;
    left: 0;
    width: 100%;
    top: 474px;
    text-align: center;
    font-size: 24px;
    line-height: 1;
  }
  .rsvp strong { font-weight: 700; }
</style>
</head>
<body>
  <main class="invitation">
    <svg class="vine-area" viewBox="0 0 1056 400" role="img" aria-label="Trailing green vine with leaves and curling tendrils sweeping across the title">
      <defs>
        <radialGradient id="vine-glow" cx="0.32" cy="0.42" r="0.55">
          <stop offset="0" stop-color="var(--leaf-deep)" stop-opacity="0.55"/>
          <stop offset="0.55" stop-color="var(--leaf-soft)" stop-opacity="0.25"/>
          <stop offset="1" stop-color="var(--leaf-soft)" stop-opacity="0"/>
        </radialGradient>
      </defs>
      <rect x="0" y="0" width="1056" height="400" fill="url(#vine-glow)"/>
    </svg>

    <svg class="title" viewBox="0 0 1056 260">
      <text x="20" y="190" textLength="1016" lengthAdjust="spacingAndGlyphs">LONG LUNCH</text>
    </svg>

    <p class="occasion">Helen's 40th</p>

    <p class="details details--when">Saturday, <strong>27th Nov 2010</strong><br>From <strong>1pm</strong></p>
    <p class="details details--venue"><strong>VENUE</strong> 214 Fernbrook Rise<br>Singapore</p>
    <p class="details details--dress">Dress <strong>Garden Glam</strong></p>

    <p class="rsvp"><strong>RSVP</strong> jolwen@quarlixmail.com by <strong>13th Nov 2010</strong></p>
  </main>
</body>
</html>
```